Computer consultant business card

Bexil Software is a newly started computer consulting company. It's a small one-man company that provides mostly Vornix applications but also websites in collaboration with designers. I'm running this company on the side of full time university studies.

I want the final design to be clean and memorable. Be creative! :)

Some inspiration:
http://www.pixelmarta.com/design/48317
http://www.pixelmarta.com/design/2739164/business-card-design-by-frostlynk
http://www.pixelmarta.com/design/604281/business-card-design-by-koralind-vestrabanu

See attachment for my company logo.
Updates

I would like to thank everyone for submitting! I'll need a couple of days to review and ultimately select a design.

Target Market(s)

Non-technical entrepreneurs and small companies.

Industry/Entity Type

University

Requirements
Must have
• My company logo.
In any way, both colors from my logo.
First- and last name, e-mail and phone number.
Double-sided design.
Nice to have
• Something creative with the symbol in my logo

```html
<!DOCTYPE html>
<html lang="en">
<head>
<meta charset="utf-8">
<title>Zuvro – Business Card</title>
<link rel="stylesheet" href="https://fonts.googleapis.com/css2?family=Jost:wght@400;500;600&family=Arimo:wght@400&display=swap">
<style>
  :root {
    --backdrop: #a98b62;
    --card-white: #ffffff;
    --ink-dark: #333133;
    --brand-blue: #4674bb;
    --card-black: #050505;
    --slate-dark: #2d2e34;
    --slate-blue: #4d5c86;
    --label-ink: #1a1510;
    --text-light: #ffffff;
  }
  * { margin: 0; padding: 0; box-sizing: border-box; }
  html, body { width: 1200px; height: 788px; overflow: hidden; }
  body {
    position: relative;
    background: var(--backdrop);
    font-family: "Jost", "Futura", sans-serif;
  }
  .side-label {
    position: absolute;
    width: 200px;
    text-align: center;
    font-family: "Arimo", Arial, sans-serif;
    font-size: 20px;
    color: var(--label-ink);
  }
  .card {
    position: absolute;
    width: 525px;
    height: 298px;
    border-radius: 20px;
    overflow: hidden;
    box-shadow: 0 3px 8px rgba(0,0,0,0.35);
  }
  .card--front, .card--back-white { background: var(--card-white); }
  .card--back-black { background: var(--card-black); }
  .card--back-slate {
    background: radial-gradient(ellipse 80% 90% at 55% 100%, var(--slate-blue) 0%, #3b4158 45%, var(--slate-dark) 100%);
  }
  .texture-glow {
    position: absolute;
    inset: 0;
    background:
      radial-gradient(ellipse 35% 35% at 28% 8%, rgba(150,150,150,0.35), transparent 70%),
      radial-gradient(ellipse 30% 35% at 85% 78%, rgba(170,150,160,0.4), transparent 70%);
  }
  .wordmark {
    position: absolute;
    left: 0; right: 0;
    display: flex;
    align-items: center;
    justify-content: center;
    gap: 22px;
  }
  .wordmark__dot {
    border-radius: 50%;
    background: var(--brand-blue);
  }
  .wordmark__name {
    font-weight: 500;
    line-height: 1;
    letter-spacing: 1px;
    color: var(--ink-dark);
  }
  .wordmark--light .wordmark__name { color: var(--text-light); }
  .wordmark--small { top: 58px; }
  .wordmark--small .wordmark__dot { width: 76px; height: 76px; }
  .wordmark--small .wordmark__name { font-size: 68px; }
  .wordmark--large { top: 96px; }
  .wordmark--large .wordmark__dot { width: 100px; height: 100px; }
  .wordmark--large .wordmark__name { font-size: 86px; }
  .web-address {
    position: absolute;
    left: 0; right: 0;
    top: 248px;
    text-align: center;
    font-size: 17px;
    letter-spacing: 3.5px;
    color: var(--ink-dark);
  }
  .web-address--light { color: var(--text-light); top: 254px; }
  .contact-band {
    position: absolute;
    left: 0; top: 200px;
    width: 525px; height: 65px;
  }
  .contact-band .band-dark { fill: var(--ink-dark); }
  .contact-band .band-blue { fill: var(--brand-blue); }
  .holder {
    position: absolute;
    left: 27px; top: 212px;
    color: var(--text-light);
  }
  .holder__name { font-size: 17px; font-weight: 600; }
  .holder__role { font-size: 13px; }
  .contact-lines {
    position: absolute;
    right: 30px; top: 209px;
    text-align: right;
    color: var(--text-light);
    font-size: 15px;
    line-height: 23px;
  }
  .contact-lines b { font-weight: 600; font-style: italic; }
</style>
</head>
<body>
  <div class="side-label" style="left:220px; top:35px;">Front</div>
  <div class="side-label" style="left:796px; top:35px;">Back - 1</div>
  <div class="side-label" style="left:225px; top:406px;">Back - 2</div>
  <div class="side-label" style="left:796px; top:406px;">Back - 3</div>

  <section class="card card--front" style="left:55px; top:75px;">
    <div class="wordmark wordmark--small">
      <span class="wordmark__dot"></span>
      <span class="wordmark__name">zuvro</span>
    </div>
    <svg class="contact-band" viewBox="0 0 525 65" aria-hidden="true">
      <polygon class="band-dark" points="0,0 245,0 300,65 0,65"/>
      <polygon class="band-blue" points="257,0 525,0 525,65 320,65"/>
    </svg>
    <div class="holder">
      <div class="holder__name">First Name Last Name</div>
      <div class="holder__role">Designation</div>
    </div>
    <div class="contact-lines">
      <div><b>p</b> : +12 345 6789</div>
      <div><b>e</b> : info@zuvrosoft.net</div>
    </div>
  </section>

  <section class="card card--back-white" style="left:622px; top:75px;">
    <div class="wordmark wordmark--large">
      <span class="wordmark__dot"></span>
      <span class="wordmark__name">zuvro</span>
    </div>
    <div class="web-address">www.zuvrosoft.net</div>
  </section>

  <section class="card card--back-black" style="left:55px; top:447px;">
    <div class="texture-glow" role="img" aria-label="Soft perforated metal texture glowing in two corners"></div>
    <div class="wordmark wordmark--large wordmark--light">
      <span class="wordmark__dot"></span>
      <span class="wordmark__name">zuvro</span>
    </div>
    <div class="web-address web-address--light">www.zuvrosoft.net</div>
  </section>

  <section class="card card--back-slate" style="left:622px; top:447px;">
    <div class="wordmark wordmark--large wordmark--light">
      <span class="wordmark__dot"></span>
      <span class="wordmark__name">zuvro</span>
    </div>
    <div class="web-address web-address--light">www.zuvrosoft.net</div>
  </section>
</body>
</html>
```